New Website Design for PHOVAN.org

We are looking for a new website design for PHOVAN.org. PHOVAN is a non profit home inspector association based in California. Home Inspectors are people that come out and look at a house before it's purchased to let the buyer know of any defects that may exist.
Our site is based on Joomla so if you'll be able to make a Joomla 3 template as well, please let us know (not required, but a bonus).
We would like to see designs that incorporate royal blue, white and chrome into the site as that's our main business colors.
We would like a place for rotating banners though they don't need to be the same size as the current site.
We would like navigation to be easier to manage with menus only across the top (via drop down menus) where we are going to sort out the items currently on the side. Possibly the front page could have a graphic link to separate portals for Realtors, Home Buyers and Inspectors, but that's just one option.
We would like a good mobile design or something that will scale easily to mobile.
The Find an Inspector feature is important and should stand out. The ASK PHOVANr site
Current home page feels a bit busy. Would like to simplify a bit.

```html
<!DOCTYPE html>
<html lang="en">
<head>
<meta charset="utf-8">
<title>PHOVAN – Pacific Home Observers &amp; Valuation Network</title>
<link rel="stylesheet" href="https://fonts.googleapis.com/css2?family=Play:wght@400;700&family=Signika:wght@400;600;700&display=swap">
<style>
:root{
  --royal:#2b3f8f;
  --royal-dark:#1e2c6b;
  --nav-top:#4a66c0;
  --nav-bottom:#2d4596;
  --footer:#1f2a5c;
  --footer-dark:#1a2350;
  --page:#efefef;
  --panel:#f8f8f8;
  --ink:#333;
  --muted:#777;
  --accent-red:#c4282a;
  --cyan:#1fa3d8;
  --line:#dcdcdc;
  --social:#9aa3b8;
}
*{margin:0;padding:0;box-sizing:border-box}
html,body{width:1067px;height:1200px;overflow:hidden}
body{background:var(--page);font-family:"Play",sans-serif;color:var(--ink);position:relative}
.abs{position:absolute}

/* header */
.top-strip{left:0;top:0;width:1067px;height:4px;background:#333}
.header{left:0;top:4px;width:1067px;height:112px;background:linear-gradient(#fff,#f4f4f4)}
.brand-mark{left:129px;top:13px;width:86px;height:86px;border-radius:50%;background:var(--royal)}
.brand-name{left:234px;top:36px;font-size:23px;line-height:29px;color:#222;letter-spacing:.5px}
.account-tab{left:745px;top:0;width:180px;height:28px;background:#2a2a2a;border-radius:0 0 4px 4px;color:#fff;font-size:13px;display:flex;align-items:center;justify-content:center;gap:12px}
.follow{left:740px;top:68px;font-size:13.5px;color:#333;display:flex;align-items:center;gap:11px}
.follow .label{margin-right:4px}
.follow .social{width:19px;height:19px;border-radius:3px;background:var(--social)}

/* nav */
.main-nav{left:0;top:116px;width:1067px;height:42px;background:linear-gradient(var(--nav-top),var(--nav-bottom));border-top:1px solid #6f86d4;border-bottom:1px solid #1d2f78}
.main-nav ul{list-style:none;display:flex;position:absolute;left:110px;top:0;height:40px;align-items:center;gap:41px;color:#fff;font-size:14.5px}

/* banner */
.hero-photo{left:98px;top:180px;width:614px;height:324px;background:linear-gradient(120deg,#8a7a62,#b9b2a4 45%,#d8d6d0 70%,#6b5b47)}
.hero-caption{left:98px;top:405px;width:454px;height:99px;background:rgba(240,240,240,.85);padding:15px 0 0 15px;font-family:"Signika",sans-serif;font-weight:600;font-size:29px;line-height:36px;letter-spacing:-1.5px;color:var(--royal);white-space:nowrap}
.hero-caption span{font-size:17px;font-weight:400;letter-spacing:-.5px;color:var(--accent-red)}
.portal{left:712px;width:257px;height:108px;background:var(--panel);border:1px solid #e2e2e2}
.portal h3{position:absolute;left:75px;top:14px;font-size:22px;font-weight:400;color:#333}
.portal p{position:absolute;left:76px;top:49px;width:172px;font-size:11px;line-height:16px;color:#666}
.portal svg{position:absolute;left:18px;top:32px}
.portal.active{background:linear-gradient(#4a62b6,#2c4191);border-color:#2c4191;left:700px;width:270px;clip-path:polygon(12px 0,100% 0,100% 100%,12px 100%,0 50%)}
.portal.active h3{left:88px;color:#fff;font-weight:700}
.portal.active p{left:89px;color:#fff}
.portal.active svg{left:31px}

/* welcome */
.welcome{left:98px;top:532px;width:871px;height:387px;background:var(--panel);border:1px solid #e4e4e4;border-top:4px solid var(--royal-dark)}
.welcome h1{position:absolute;left:22px;top:26px;font-size:21px;font-weight:400;color:var(--royal)}
.welcome .intro{position:absolute;left:23px;top:64px;width:545px;font-size:13.2px;line-height:20.5px;color:var(--muted)}
.work-photo{left:588px;top:29px;width:264px;height:130px;background:linear-gradient(100deg,#7a5330,#c59a64 45%,#e1d6c4 70%,#8d6b45)}
.divider{left:0;top:187px;width:869px;height:1px;background:var(--line)}
.col h2{font-size:17px;font-weight:400;color:var(--royal);margin-bottom:14px}
.col-search{left:24px;top:212px;width:250px}
.col-search p{font-size:12px;line-height:17px;color:#555}
.zip{margin-top:15px;width:250px;height:28px;border:1px solid #ccc;border-top-color:#999;background:#fff;font-size:13px;color:#555;padding:4px 10px}
.btn-search{margin-top:15px;display:inline-block;background:var(--royal);color:#fff;font-size:12px;font-weight:700;padding:2px 8px}
.col-news{left:298px;top:212px;width:280px}
.news-item{margin-bottom:10px;font-size:12px;line-height:14px;color:#444}
.news-item small{display:block;font-size:10.5px;color:#555}
.col-testi{left:584px;top:212px;width:270px}
.testi{position:relative;height:69px;padding-left:62px;font-size:11.5px;line-height:15px;color:#666}
.testi .avatar{position:absolute;left:0;top:2px;width:52px;height:48px;background:linear-gradient(#d9c2ad,#8a7765)}
.testi b{display:block;font-weight:400;color:#555;margin-bottom:3px}
.testi time{position:absolute;right:0;top:34px;font-size:9.5px;color:var(--royal)}

/* footer */
.footer{left:0;top:945px;width:1067px;height:203px;background:var(--footer)}
.footer h2{font-size:17.5px;font-weight:400;color:#fff;margin-bottom:9px}
.footer p,.footer li{font-size:11.5px;line-height:20px;color:#dfe3f2;list-style:none}
.f-login{left:112px;top:40px;width:170px}
.field{width:166px;height:25px;border-radius:3px;background:linear-gradient(#fff,#e7e7e7);font-size:10.5px;color:#666;padding:6px 9px;margin-bottom:9px}
.f-login p{margin:-3px 0 6px 7px}
.login-btn{display:inline-block;margin-left:1px;background:linear-gradient(#fff,#e4e4e4);border-radius:3px;color:#333;font-size:12px;padding:3px 15px}
.f-testi{left:330px;top:36px;width:215px}
.f-testi .who{color:var(--cyan);margin-top:10px}
.f-map{left:588px;top:36px;width:180px}
.f-contact{left:776px;top:36px;width:200px}
.bottom-bar{left:0;top:1148px;width:1067px;height:52px;background:var(--footer-dark);border-top:1px solid #121a3d;color:#fff;font-size:11px;letter-spacing:-.2px}
.bottom-bar .copy{position:absolute;left:111px;top:17px}
.bottom-bar ul{position:absolute;right:110px;top:17px;display:flex;gap:13px;list-style:none}
</style>
</head>
<body>
<div class="abs top-strip"></div>

<header class="abs header">
  <div class="abs brand-mark"></div>
  <div class="abs brand-name">Pacific Home Observers &amp;<br>Valuation Network</div>
  <div class="abs follow"><span class="label">FOLLOW US</span>
    <span class="social"></span><span class="social"></span><span class="social"></span><span class="social"></span>
  </div>
</header>
<div class="abs account-tab"><span>Inspector Login</span><span>|</span><span>Sign Up</span></div>

<nav class="abs main-nav">
  <ul>
    <li>Home</li><li>Find an Inspector</li><li>Home Buyers &amp; Sellers</li><li>Real Estate Agents</li><li>Inspectors</li><li>Ask PHOVAN</li><li>Conferences</li>
  </ul>
</nav>

<section>
  <div class="abs hero-photo" role="img" aria-label="Photo of two inspectors examining the interior wall framing of a house"></div>
  <div class="abs hero-caption">Lorem Ipsum est simplement du faux<br>texte employé dans sition. <span>Learn More</span></div>

  <a class="abs portal" style="top:181px">
    <svg width="40" height="40" viewBox="0 0 40 40"><path d="M4 18 L20 4 L36 18 H31 V34 H9 V18Z" fill="#222"/><circle cx="22" cy="26" r="5" fill="#fff" stroke="#222" stroke-width="3"/><rect x="26" y="24.5" width="12" height="3" fill="#222"/></svg>
    <h3>Home Buyers</h3>
    <p>Lorem Ipsum est simplement du faux texte employé dans sition et la misen page avantimpression.</p>
  </a>
  <a class="abs portal active" style="top:289px">
    <svg width="40" height="40" viewBox="0 0 40 40"><path d="M4 18 L20 4 L36 18 H31 V34 H9 V18Z" fill="none" stroke="#fff" stroke-width="3"/><circle cx="21" cy="24" r="6" fill="none" stroke="#fff" stroke-width="2.5"/><path d="M25 28 L33 36" stroke="#fff" stroke-width="3"/></svg>
    <h3>Inspectors</h3>
    <p>Lorem Ipsum est simplement du faux texte employé dans sition et la misen page avantimpression.</p>
  </a>
  <a class="abs portal" style="top:397px">
    <svg width="40" height="40" viewBox="0 0 40 40"><path d="M4 18 L20 4 L36 18Z" fill="#222"/><rect x="3" y="18" width="34" height="18" fill="#222"/><rect x="8" y="22" width="24" height="11" fill="#fff"/><text x="20" y="32" font-size="11" text-anchor="middle" font-family="Play,sans-serif" font-weight="700" fill="#222">$</text></svg>
    <h3>Realtors</h3>
    <p>Lorem Ipsum est simplement du faux texte employé dans sition et la misen page avantimpression.</p>
  </a>
</section>

<main class="abs welcome">
  <h1>Welcome to Pacific Home Observers &amp; Valuation Network</h1>
  <p class="intro">Lorem Ipsum est simplement du faux texte employé dans la sition et la misen page avant impression. Le Lorem Ipsum est le faux texte standard de l'imprimerie depuis les années 1500, quand un peintre anonyme assembla ensemble des morceaux de texte pour réaliser un livre spécimen de polices de texte. mais s'est aussi adapté bureautique informatique, sans que son contenu n'en soit modifié. Popularisé dans les années 1960.</p>
  <div class="abs work-photo" role="img" aria-label="Photo of inspectors checking an exposed wall during a renovation"></div>
  <div class="abs divider"></div>

  <div class="abs col col-search">
    <h2>Search for Inspector</h2>
    <p>Lorem Ipsum est simplement du faux texte employé dans.</p>
    <div class="zip">Enter your Zip Code</div>
    <span class="btn-search">Search</span>
  </div>

  <div class="abs col col-news">
    <h2>News &amp; Events</h2>
    <div class="news-item">Praesent luptatum ril delenit augue duis dolore<small>Yesterday at 08:23:14 PM</small></div>
    <div class="news-item">Praesent luptatum ril delenit augue duis dolore<small>Yesterday at 07:58:35 PM</small></div>
    <div class="news-item">Praesent luptatum ril delenit augue duis dolore<small>Yesterday at 07:11:19 PM</small></div>
  </div>

  <div class="abs col col-testi">
    <h2>Testimonials</h2>
    <div class="testi"><div class="avatar" role="img" aria-label="Portrait of a client"></div><b>Marlon Fitch</b>On sait depuis longtemps que travailler avec du texte lisible<time>14-12-2012</time></div>
    <div class="testi"><div class="avatar" role="img" aria-label="Portrait of a client"></div><b>Marlon Fitch</b>On sait depuis longtemps que travailler avec du texte lisible<time>14-12-2012</time></div>
  </div>
</main>

<footer class="abs footer">
  <div class="abs f-login">
    <h2>Inspector Login</h2>
    <div class="field">username</div>
    <div class="field">password</div>
    <p>Forgot your password</p>
    <span class="login-btn">Log in</span>
  </div>
  <div class="abs f-testi">
    <h2>Testimonials</h2>
    <p style="line-height:15px">Lorem Ipsum est simplement du faux texte employé.</p>
    <p style="line-height:15px;margin-top:14px">If you want us to design your colour chart contact us</p>
    <p class="who">Marlon Fitch</p>
  </div>
  <div class="abs f-map">
    <h2>Site Map</h2>
    <ul><li>Praesent luptatum delen</li><li>it augue duis dolore</li><li>Praesent luptatum delen</li><li>it augue duis dolore</li><li>Praesent luptatum delen</li></ul>
  </div>
  <div class="abs f-contact">
    <h2>Contact Details</h2>
    <p style="line-height:15px">Contact details will be appear here contact details here</p>
    <p style="margin-top:10px">Phone No. : 00 555 410-7788</p>
    <p style="margin-top:10px">E-mail : info@phovan.org</p>
  </div>
</footer>
<div class="abs bottom-bar">
  <span class="copy">Pacific Home Observers &amp; Valuation Network. All Rights Reserved</span>
  <ul><li>Find an Inspector</li><li>Home Buyers &amp; Sellers</li><li>Real Estate Agents</li></ul>
</div>
</body>
</html>
```